Business Card

Just need business logo with phone number on it. 0487 312 654
And the following on the bottom of the card.

"Your local plumbing experts".
and emblems for zelpa card, cheque and cash

```html
<!DOCTYPE html>
<html lang="en">
<head>
<meta charset="utf-8">
<title>Harbourline Plumbing &amp; Drainage — Business Card</title>
<link rel="stylesheet" href="https://fonts.googleapis.com/css2?family=Michroma&family=Roboto:wght@400;500&display=swap">
<style>
  :root {
    --stage: #e5e5e5;
    --card: #f9f9f9;
    --brand-red: #e0231c;
    --brand-blue: #0f78c4;
    --ink: #3a3a3a;
    --cheque-yellow: #f6e58c;
    --cash-green: #8fb99a;
    --white: #ffffff;
  }
  * { box-sizing: border-box; margin: 0; padding: 0; }
  html, body { width: 1200px; height: 608px; overflow: hidden; }
  body { background: var(--stage); position: relative; font-family: "Roboto", sans-serif; }

  .card {
    position: absolute;
    top: 206px;
    width: 327px;
    height: 197px;
    background: var(--card);
    overflow: hidden;
  }
  .card--front { left: 237px; }
  .card--back { left: 635px; }

  .wordmark {
    position: absolute;
    left: 0; right: 0;
    text-align: center;
    font-family: "Michroma", sans-serif;
    color: var(--brand-red);
    text-transform: uppercase;
    line-height: 1.25;
  }
  .wordmark__name { display: block; font-size: 17px; letter-spacing: 1px; }
  .wordmark__trade { display: block; font-size: 7.4px; letter-spacing: 1.6px; }
  .card--front .wordmark { top: 80px; }
  .card--back .wordmark { top: 34px; transform: scale(0.88); }

  .phone {
    position: absolute;
    top: 116px; left: 0; right: 0;
    text-align: center;
    font-family: "Michroma", sans-serif;
    font-size: 19px;
    letter-spacing: 1px;
    color: var(--ink);
    -webkit-text-stroke: 0.6px var(--ink);
  }

  .payments {
    position: absolute;
    left: 13px; top: 171px;
    display: flex; align-items: center; gap: 4px;
  }
  .payments__card {
    height: 11px; padding: 0 3px;
    border: 0.6px solid #b7b7b7;
    background: var(--white);
    font-size: 6px; font-weight: 500;
    color: var(--brand-blue);
    line-height: 10px;
  }
  .payments__cheque { width: 25px; height: 11px; background: var(--cheque-yellow); }
  .payments__cash { width: 21px; height: 11px; background: var(--cash-green); border-radius: 2px; transform: rotate(-6deg); margin-left: 4px; }

  .footer-band { position: absolute; left: 0; bottom: 0; width: 327px; height: 18px; }
  .tagline {
    position: absolute;
    left: 192px; bottom: 3px;
    font-size: 9.6px;
    line-height: 12px;
    color: var(--white);
    white-space: nowrap;
  }
</style>
</head>
<body>
  <section class="card card--front" aria-label="Card front">
    <div class="wordmark">
      <span class="wordmark__name">Harbourline</span>
      <span class="wordmark__trade">Plumbing &amp; Drainage</span>
    </div>
  </section>

  <section class="card card--back" aria-label="Card back">
    <div class="wordmark">
      <span class="wordmark__name">Harbourline</span>
      <span class="wordmark__trade">Plumbing &amp; Drainage</span>
    </div>

    <p class="phone">0487 312 654</p>

    <div class="payments" aria-label="Accepted payments">
      <span class="payments__card">zelpa</span>
      <span class="payments__cheque" aria-label="Cheque"></span>
      <span class="payments__cash" aria-label="Cash"></span>
    </div>

    <svg class="footer-band" viewBox="0 0 327 18" aria-hidden="true">
      <rect x="0" y="10" width="162" height="8" fill="var(--brand-blue)"/>
      <polygon points="158,18 178,0 327,0 327,18" fill="var(--brand-red)"/>
    </svg>
    <p class="tagline">Your local plumbing experts</p>
  </section>
</body>
</html>
```